Postcard Design

We are an upscale, full service real estate boutique based in Mt. Pleasant, SC. We will be having a Grand Opening of our beautiful, new office complete with high end custom home architecture and design. I will attach photos for your review. I would like to come up with a medium postcard to be mailed to clientele of Mt. Pleasant. Home prices between $300,000 - $2.2 million. The customers can call our office for the Grand Opening Listing Promotion or stop by our grand opening. We will have drawings for door prizes that include services at Brisklane Day Spa, Tangy Pepperpot gift certificates, and they can register to win a cruise with a listing presentation. Our Grand Opening will be a couple of different dates, April 7, 2016 and April 21, 2016. I will want an order that lists the 7th and another order that will list the 21. The look should have a very "relaxing, beach" feel, but not Myrtle Beach...should reflect colors of the ocean, like you are on vacation. I will include logos and pics for your review. Thank you!

```html
<!DOCTYPE html>
<html lang="en">
<head>
<meta charset="utf-8">
<title>Harborpine Real Estate – Grand Opening Postcard</title>
<link href="https://fonts.googleapis.com/css2?family=EB+Garamond:ital,wght@1,400;1,500&family=Montserrat:wght@400;500;600;700&display=swap" rel="stylesheet">
<style>
  :root {
    --stage: #000000;
    --paper: #ffffff;
    --deep-blue: #0a7bc1;
    --sea-blue: #00a9d8;
    --panel-blue: #229fdc;
    --tab-blue: #0d85cc;
    --ink: #111111;
    --photo-sky: #8fb4cf;
    --photo-house: #9fb3c6;
  }
  * { box-sizing: border-box; margin: 0; padding: 0; }
  html, body { width: 914px; height: 1200px; overflow: hidden; background: var(--stage); }
  body { position: relative; font-family: "Montserrat", Arial, sans-serif; }

  .card { position: absolute; left: 16px; width: 878px; height: 567px; background: var(--paper); overflow: hidden; }
  .card--front { top: 18px; }
  .card--back { top: 600px; }

  .front-art { position: absolute; inset: 0; width: 878px; height: 567px; }

  .brand { position: absolute; left: 16px; top: 168px; padding: 6px 14px 8px 8px; background: var(--paper); border-radius: 0 10px 10px 0; }
  .brand__row { display: flex; align-items: center; gap: 8px; }
  .brand__dot { width: 16px; height: 16px; border-radius: 50%; background: var(--sea-blue); }
  .brand__name { font-weight: 700; font-size: 28px; letter-spacing: 1.5px; color: var(--deep-blue); text-transform: uppercase; line-height: 1; }
  .brand__sub { margin: 7px 0 0 30px; font-weight: 700; font-size: 12px; letter-spacing: 5px; color: var(--deep-blue); line-height: 1; }

  .opening { position: absolute; left: 24px; top: 252px; font-family: "EB Garamond", Georgia, serif; font-style: italic; font-size: 22.5px; line-height: 38px; color: var(--ink); }
  .opening__dates { color: var(--deep-blue); font-weight: 500; }

  .intro { position: absolute; left: 24px; top: 386px; font-weight: 600; font-size: 15.5px; line-height: 28.5px; color: var(--ink); white-space: nowrap; }

  .prices { position: absolute; right: 17px; top: 457px; text-align: right; color: var(--deep-blue); font-weight: 700; }
  .prices__label { font-size: 15.5px; color: var(--sea-blue); letter-spacing: 0.2px; }
  .prices__range { font-size: 27px; line-height: 1.2; }

  .contact-band { position: absolute; left: 0; bottom: 0; width: 100%; height: 43px; background: var(--sea-blue); color: var(--paper); display: flex; justify-content: space-between; align-items: center; padding: 0 15px 0 24px; font-weight: 700; font-size: 20px; letter-spacing: 0.6px; }

  .details-panel { position: absolute; left: 0; top: 0; width: 440px; height: 497px; background: var(--panel-blue); color: var(--paper); }
  .details-panel__tab { position: absolute; left: 0; top: 12px; width: 330px; height: 40px; background: var(--tab-blue); clip-path: polygon(0 0, 290px 0, 100% 100%, 0 100%); }
  .details-panel__title { position: absolute; left: 24px; top: 19px; font-weight: 600; font-size: 22px; }
  .details-panel__body { position: absolute; left: 24px; top: 68px; font-weight: 600; font-size: 16px; line-height: 25px; }
  .details-panel__name { font-size: 22px; line-height: 30px; margin-bottom: 2px; }
  .details-panel__phones { margin-top: 25px; }

  .mail-address { position: absolute; left: 469px; top: 23px; font-size: 9.5px; line-height: 14px; color: var(--ink); font-style: normal; }
  .mail-address__name { font-weight: 700; }
  .postage { position: absolute; left: 793px; top: 16px; width: 64px; height: 64px; border: 1px solid #555; display: flex; align-items: center; justify-content: center; font-size: 9.5px; color: var(--ink); }
</style>
</head>
<body>

<section class="card card--front">
  <svg class="front-art" viewBox="0 0 1024 662" preserveAspectRatio="none">
    <defs>
      <linearGradient id="photoTone" x1="0" y1="0" x2="0" y2="1">
        <stop offset="0" stop-color="var(--photo-sky)"/>
        <stop offset="0.55" stop-color="var(--photo-house)"/>
        <stop offset="1" stop-color="#8a7a5e"/>
      </linearGradient>
    </defs>
    <polygon points="0,0 135,0 718,545 0,56" fill="var(--deep-blue)"/>
    <polygon role="img" aria-label="Photo of a two-storey blue clapboard home among trees" points="155,0 1024,0 1024,252 727,540" fill="url(#photoTone)"/>
    <polygon points="1024,268 1024,325 745,550 734,550" fill="var(--sea-blue)"/>
  </svg>

  <div class="brand">
    <div class="brand__row"><span class="brand__dot"></span><span class="brand__name">Harborpine</span></div>
    <div class="brand__sub">REAL ESTATE</div>
  </div>

  <p class="opening">
    Our Grand Opening will<br>
    be a couple of different dates,<br>
    <span class="opening__dates">April 7, 2016 and April 21, 2016.</span>
  </p>

  <p class="intro">We are an upscale, full service real estate boutique<br>based in Mt. Pleasant, SC.&nbsp; We will be having a<br>Grand Opening of our beautiful, new office complete with high<br>end custom home architecture and design</p>

  <div class="prices">
    <div class="prices__label">HOME PRICES BETWEEN</div>
    <div class="prices__range">$3LACS TO $2.2 M</div>
  </div>

  <div class="contact-band">
    <span>WEBSITE : WWW.HARBORPINE.COM</span>
    <span>CALL US AT :&nbsp; +1 843 555 0147</span>
  </div>
</section>

<section class="card card--back">
  <div class="details-panel">
    <div class="details-panel__tab"></div>
    <h2 class="details-panel__title">Our Contact Details :</h2>
    <div class="details-panel__body">
      <div class="details-panel__name">Harborpine</div>
      <div>1180 Harbor Point, Suite 200</div>
      <div>512 Coleman Boulevard</div>
      <div>Mt. Pleasant, SC 29464</div>
      <div class="details-panel__phones">TEL: 843-555-0130 or 843-555-0162</div>
      <div>FAX: 843-555-0189</div>
    </div>
  </div>

  <address class="mail-address">
    <div class="mail-address__name">Harborpine</div>
    <div>1180 Harbor Point, Suite 200</div>
    <div>512 Coleman Boulevard</div>
    <div>Mt. Pleasant, SC 29464</div>
  </address>

  <div class="postage">POSTAGE</div>
</section>

</body>
</html>
```